Business Card Design Project

i need a bussines car design
Velora Clinical Hypnotherapy

Daniel Wexford
Psychotherapy & Hypnosis

84261937 /0427591628

back of the card appoinment space.

file was provided on a PDF, LOgo , use the blu colorsa as well , elegant, clear,

Target Market(s)

young professional, caucasian , young mothers.

Industry/Entity Type

Business

```html
<!DOCTYPE html>
<html lang="en">
<head>
<meta charset="utf-8">
<title>Velora Clinical Hypnotherapy – Business Card</title>
<link rel="stylesheet" href="https://fonts.googleapis.com/css2?family=Arimo:wght@400;700&family=Jost:wght@300;400;500&family=Archivo+Black&display=swap">
<style>
  :root {
    --stage: #a7a8ac;
    --label: #8d8e92;
    --blue-deep: #0b3f8c;
    --blue-mid: #1d6fc4;
    --blue-sky: #4aa3e6;
    --blue-pale: #9fd2f5;
    --logo-blue: #8fc8f2;
    --white: #ffffff;
    --ink: #1a1a1a;
    --bar: #231f20;
    --badge: #c8d84a;
  }
  * { box-sizing: border-box; margin: 0; padding: 0; }
  html, body { width: 1200px; height: 1000px; overflow: hidden; }
  body { background: var(--stage); position: relative; font-family: "Jost", sans-serif; }

  .side-label {
    position: absolute;
    font-family: "Archivo Black", sans-serif;
    font-size: 64px;
    letter-spacing: 1px;
    color: var(--label);
  }
  .side-label--front { left: 92px; top: 205px; }
  .side-label--back { left: 622px; top: 628px; }

  .card {
    position: absolute;
    top: 290px;
    width: 520px;
    height: 318px;
    overflow: hidden;
    box-shadow: 0 3px 8px rgba(0,0,0,.35);
  }

  /* FRONT */
  .card--front {
    left: 80px;
    background: linear-gradient(180deg, #2f84d4 0%, var(--blue-mid) 30%, #2b86d6 55%, #4c9fe2 66%);
  }
  .front__top-band {
    position: absolute; left: 0; top: 0; width: 100%; height: 48px;
    background: linear-gradient(180deg, var(--blue-deep), #1b5fb4);
  }
  .front__sheen {
    position: absolute; left: 0; top: 48px; width: 100%; height: 18px;
    background: linear-gradient(180deg, rgba(255,255,255,.25), rgba(255,255,255,0));
  }
  .front__name {
    position: absolute; right: 26px; top: 12px;
    font-family: "Arimo", sans-serif; font-size: 29px; color: var(--white);
    letter-spacing: .5px;
  }
  .front__portrait {
    position: absolute; left: 0; top: 14px; width: 300px; height: 200px;
    background: linear-gradient(180deg, #6b5a4e 0%, #c99a7c 35%, #e8d8c8 70%, #f1e7dc 100%);
  }
  .front__phone {
    position: absolute; right: 30px; top: 133px;
    display: flex; align-items: center; gap: 12px;
    font-family: "Arimo", sans-serif; font-size: 17px; color: var(--white);
  }
  .front__base {
    position: absolute; left: 0; bottom: 0; width: 100%; height: 106px;
    background: linear-gradient(180deg, #114b9b 0%, var(--blue-deep) 60%, #08326f 100%);
    border-top: 2px solid var(--blue-sky);
  }
  .brand {
    position: absolute; left: 22px; top: 18px;
    display: flex; align-items: center; gap: 12px;
  }
  .brand__dot {
    width: 34px; height: 34px; border-radius: 50%; background: var(--logo-blue);
  }
  .brand__name {
    font-family: "Jost", sans-serif; font-weight: 300; font-size: 30px;
    color: var(--logo-blue); letter-spacing: .3px;
  }
  .front__web {
    position: absolute; left: 134px; top: 64px;
    font-family: "Arimo", sans-serif; font-size: 14px; color: var(--white);
  }
  .front__badge {
    position: absolute; right: 22px; top: 22px;
    width: 56px; height: 56px; border-radius: 50%;
    background: var(--badge); border: 3px solid #dfe6ea;
  }

  /* BACK */
  .card--back { left: 620px; background: var(--white); }
  .back__header {
    height: 62px; background: var(--bar); color: var(--white);
    display: flex; align-items: center; justify-content: center;
    font-size: 19px; font-weight: 400; letter-spacing: 1.5px;
  }
  .appointments { list-style: none; padding: 14px 28px 0 26px; }
  .appointment {
    display: flex; align-items: flex-end; height: 37px;
    font-size: 15px; color: var(--ink);
  }
  .appointment__no { width: 16px; }
  .blank { display: inline-block; border-bottom: 1px solid var(--ink); height: 14px; margin: 0 5px 3px; }
  .blank--time { width: 42px; }
  .blank--note { width: 170px; margin-left: 8px; }
  .blank--date { width: 30px; margin: 0 2px 3px; }
  .appointment__date { margin-left: 12px; display: flex; align-items: flex-end; }
  .back__footer {
    position: absolute; left: 0; bottom: 0; width: 100%; height: 54px;
    background: var(--bar); color: var(--white);
    display: flex; align-items: center; justify-content: center;
    font-size: 13.5px;
  }
</style>
</head>
<body>
  <div class="side-label side-label--front">FRONT</div>

  <section class="card card--front" aria-label="Business card front">
    <div class="front__top-band"></div>
    <div class="front__sheen"></div>
    <div class="front__portrait" role="img" aria-label="Portrait photograph of the therapist"></div>
    <h1 class="front__name">DANIEL WEXFORD</h1>
    <p class="front__phone">84261937 /0427591628
      <svg width="22" height="22" viewBox="0 0 22 22" aria-hidden="true">
        <rect x="1" y="1" width="20" height="20" rx="4" fill="#1a2a44"/>
        <path d="M7 5c-1 0-2 1-2 2 0 5 5 10 10 10 1 0 2-1 2-2l-2.5-2-1.8 1.2c-1.6-.8-3.1-2.3-3.9-3.9L10 8.5 8 5z" fill="#fff"/>
      </svg>
    </p>
    <div class="front__base">
      <div class="brand">
        <span class="brand__dot"></span>
        <span class="brand__name">Velora Hypnotherapy</span>
      </div>
      <p class="front__web">www.veloraclinicalhypnotherapy.com.au</p>
      <div class="front__badge" role="img" aria-label="Professional association badge"></div>
    </div>
  </section>

  <section class="card card--back" aria-label="Business card back">
    <header class="back__header">VELORA Clinical Hypnotherapy</header>
    <ol class="appointments">
      <li class="appointment"><span class="appointment__no">1</span><span class="blank blank--time"></span>am/pm<span class="blank blank--note"></span><span class="appointment__date"><span class="blank blank--date"></span>/<span class="blank blank--date"></span>/<span class="blank blank--date"></span></span></li>
      <li class="appointment"><span class="appointment__no">2</span><span class="blank blank--time"></span>am/pm<span class="blank blank--note"></span><span class="appointment__date"><span class="blank blank--date"></span>/<span class="blank blank--date"></span>/<span class="blank blank--date"></span></span></li>
      <li class="appointment"><span class="appointment__no">3</span><span class="blank blank--time"></span>am/pm<span class="blank blank--note"></span><span class="appointment__date"><span class="blank blank--date"></span>/<span class="blank blank--date"></span>/<span class="blank blank--date"></span></span></li>
      <li class="appointment"><span class="appointment__no">4</span><span class="blank blank--time"></span>am/pm<span class="blank blank--note"></span><span class="appointment__date"><span class="blank blank--date"></span>/<span class="blank blank--date"></span>/<span class="blank blank--date"></span></span></li>
      <li class="appointment"><span class="appointment__no">5</span><span class="blank blank--time"></span>am/pm<span class="blank blank--note"></span><span class="appointment__date"><span class="blank blank--date"></span>/<span class="blank blank--date"></span>/<span class="blank blank--date"></span></span></li>
    </ol>
    <footer class="back__footer">By Appointment&nbsp; Phone: 0427 591 628 | 48 Harlow Street, Kensington 3031</footer>
  </section>

  <div class="side-label side-label--back">BACK</div>
</body>
</html>
```